diesel mechanic business card design

granite diesel is a new and upcoming business we are looking for some bad ass designs to help get us started we offer 24 hour road service, off road recovery, welding and custom fabrications we are diesel mechanics so our design should be bold and eye catching flames wrenches engine parts are cool we work in an industrial environment around heavy trucks and equipment this in not a quick grease we fix it all nothing is to big or to small the colors red and black are always a plus but we are open to anything you guys can come up with ready set go

Target Market(s)

other small business primarily trucking and transportation companys

Industry/Entity Type

Business

Contact Information for Business Card

company name Granitte diesel truck & trailer repair / address 14 rear north halloway ave kessler falls OH 43999 / ownersAdam DeLuccie 570-555-0143 / Walter Dombrosky 570-555-0178 E mail brentkovalsky@mailbox-example.com fax 570-555-0192

Requirements
Nice to have
• industrial modern design
Should not have
• rainbows butterfly's unicorns or cupcakes

```html
<!DOCTYPE html>
<html lang="en">
<head>
<meta charset="utf-8">
<title>Granitte Diesel Business Card</title>
<link href="https://fonts.googleapis.com/css2?family=Oswald:wght@700&family=Open+Sans:wght@300;400&display=swap" rel="stylesheet">
<style>
  :root {
    --page: #e8e5e0;
    --orange-light: #f7c23a;
    --orange-mid: #f2a62a;
    --orange-deep: #e48a1c;
    --ink: #161616;
    --band: #f4f4f2;
    --band-edge: #1b1b1b;
    --photo-sky: #bcd4e6;
    --photo-red: #b8322c;
    --photo-dark: #2f3336;
  }
  * { margin: 0; padding: 0; box-sizing: border-box; }
  html, body { width: 1200px; height: 892px; overflow: hidden; background: var(--page); }
  .sheet {
    width: 1200px; height: 892px;
    display: flex; flex-direction: column; align-items: center; justify-content: center; gap: 36px;
  }
  .card {
    position: relative; width: 700px; height: 400px; overflow: hidden;
    background: linear-gradient(135deg, var(--orange-deep) 0%, var(--orange-mid) 35%, var(--orange-light) 70%, var(--orange-mid) 100%);
    box-shadow: 0 6px 18px rgba(0,0,0,.18);
  }
  .company {
    font-family: "Oswald", "Arial Narrow", sans-serif; font-weight: 700;
    color: var(--ink); text-transform: uppercase; text-align: center;
    line-height: 1.05; letter-spacing: .5px; white-space: nowrap;
  }
  /* front */
  .front .company { position: absolute; top: 48px; left: 0; right: 0; font-size: 36px; }
  .owners-band {
    position: absolute; top: 158px; left: 0; right: 0; height: 96px;
    background: var(--band);
    border-top: 6px solid var(--band-edge); border-bottom: 6px solid var(--band-edge);
    display: grid; grid-template-columns: 1fr auto 1fr; align-items: center; padding: 0 60px;
    font-family: "Open Sans", Arial, sans-serif; color: var(--ink);
  }
  .owner { font-weight: 300; font-size: 25px; line-height: 1.15; }
  .owner .phone { display: block; font-size: 19px; padding-left: 34px; }
  .owner.right { justify-self: end; }
  .owners-label { font-size: 14px; font-weight: 400; }
  .contact {
    position: absolute; top: 282px; left: 200px;
    font-family: "Open Sans", Arial, sans-serif; font-size: 16px; color: var(--ink); line-height: 1.45;
  }
  .contact li { list-style: none; display: flex; align-items: center; gap: 7px; }
  .contact svg { width: 13px; height: 13px; fill: #fff; }
  /* back */
  .photo {
    position: absolute; top: 0; bottom: 0; left: 0; width: 230px;
    background: linear-gradient(180deg, var(--photo-sky) 0%, var(--photo-red) 35%, #8d4a3a 55%, var(--photo-dark) 100%);
  }
  .photo-divider { position: absolute; top: 0; bottom: 0; left: 230px; width: 14px; background: var(--band-edge); }
  .back .company { position: absolute; top: 0; bottom: 0; left: 244px; right: 0;
    display: flex; flex-direction: column; justify-content: center; font-size: 29px; }
</style>
</head>
<body>
<main class="sheet">
  <section class="card front">
    <h1 class="company">Granitte Diesel Truck &amp; Trailer<br>Repair</h1>
    <div class="owners-band">
      <p class="owner">Brent Kovalsky<span class="phone">570-555-0143</span></p>
      <p class="owners-label">owners</p>
      <p class="owner right">Walter Dombrosky<span class="phone">570-555-0178</span></p>
    </div>
    <ul class="contact">
      <li><svg viewBox="0 0 16 16" aria-hidden="true"><rect x="1" y="6" width="14" height="8" rx="1"/><rect x="4" y="1" width="8" height="5"/></svg>570-555-0192</li>
      <li><svg viewBox="0 0 16 16" aria-hidden="true"><path d="M1 3h14v10H1z M1 3l7 6 7-6" stroke="#f2a62a" stroke-width="1"/></svg>brentkovalsky@mailbox-example.com</li>
      <li>14 rear north halloway ave kessler falls OH 43999</li>
    </ul>
  </section>
  <section class="card back">
    <div class="photo" role="img" aria-label="Photo of a red semi truck above an open diesel engine bay"></div>
    <div class="photo-divider"></div>
    <h2 class="company">Granitte Diesel Truck &amp; Trailer<br>Repair</h2>
  </section>
</main>
</body>
</html>
```